Creative, fresh business card design for Ripplecraft Facades

We need a fresh, creative business card design for Ripplecraft Facades. We are the manufacturer of Ripplecraft Facades in Australia. Wall panels are 2400 x 1200mm panels made from MDF and feature 3D patterns on the face of the panel. The colours to be used are green, silver/grey and white RGB
Red 187
Green 207
Blue 65.

An idea is to possibly use a watermark of one of our designs as a background (like on the "Grids" design on the left hand side of page 2 of our brochure).

Target Market(s)

Interior designers, architects, builders and home renovators

Industry/Entity Type

Business

Contact Information for Business Card

Details to go on the card are:
Our logo (attached),
Slogan: "Decorative panels for interiors and exteriors",
Contact name,
Position,
Mobile phone number,
Business address,
Business phone,
Business fax,
Website and
Email address.

I have attached a few images of our panels and our brochure for reference.

The colours of the business card should feature our logo colours which are: RGB
Red 187
Green 207
Blue 65

Requirements
Must have
• Very modern fonts and design. Some of the designs shown especially the "Prisms" design which is a popular design.
Nice to have
• Creative but simple design. Very contemporary.
Should not have
• Anything ornate or old fashioned.

```html
<!DOCTYPE html>
<html lang="en">
<head>
<meta charset="utf-8">
<title>Ripplecraft Facades – Business Card</title>
<link rel="stylesheet" href="https://fonts.googleapis.com/css2?family=Advent+Pro:wght@400&family=Raleway:wght@400&display=swap">
<style>
  :root {
    --card-grey: #95a9a8;
    --card-grey-deep: #8a9ea0;
    --stripe-green: #b8f500;
    --icon-green: #b4ef1a;
    --ink-white: #ffffff;
  }
  html, body {
    margin: 0;
    padding: 0;
    width: 1200px;
    height: 666px;
    overflow: hidden;
    background: var(--card-grey);
  }
  .card {
    position: relative;
    width: 1200px;
    height: 666px;
    overflow: hidden;
    background: var(--card-grey);
  }
  .card__backdrop {
    position: absolute;
    inset: 0;
    background: linear-gradient(125deg, var(--card-grey) 0%, var(--card-grey-deep) 45%, var(--card-grey) 70%, var(--card-grey-deep) 100%);
  }
  .card__stripe {
    position: absolute;
    inset: 0;
  }
  .identity {
    position: absolute;
    left: 104px;
    top: 266px;
    color: var(--ink-white);
    font-family: "Advent Pro", sans-serif;
    font-weight: 400;
  }
  .identity__name {
    margin: 0;
    font-weight: 400;
    line-height: 1;
    white-space: nowrap;
  }
  .identity__first { font-size: 86px; letter-spacing: 2px; }
  .identity__last { font-size: 66px; margin-left: 26px; letter-spacing: 1px; }
  .identity__position {
    margin: 10px 0 0 120px;
    font-size: 46px;
    line-height: 1;
  }
  .contact {
    position: absolute;
    left: 736px;
    top: 0;
    margin: 0;
    padding: 0;
    list-style: none;
    color: var(--ink-white);
    font-family: "Raleway", sans-serif;
    font-variant-numeric: lining-nums;
  }
  .contact__item {
    position: absolute;
    left: 0;
    display: flex;
    align-items: flex-start;
    white-space: nowrap;
    line-height: 1.25;
  }
  .contact__icon {
    width: 30px;
    height: 30px;
    flex: none;
    margin-right: 6px;
    fill: var(--icon-green);
    stroke: var(--icon-green);
  }
  .contact__item--mobile { top: 190px; font-size: 38px; }
  .contact__item--mobile .contact__icon { margin-top: 9px; }
  .contact__item--address { top: 246px; font-size: 28px; line-height: 35px; }
  .contact__item--email { top: 314px; font-size: 28px; }
  .contact__item--phone { top: 352px; font-size: 38px; }
  .contact__item--phone .contact__icon,
  .contact__item--fax .contact__icon { margin-top: 9px; }
  .contact__item--fax { top: 400px; font-size: 38px; }
  .contact__item--web { top: 456px; font-size: 28px; }
  .contact__item--web .contact__icon { margin-top: 3px; }
</style>
</head>
<body>
<main class="card">
  <div class="card__backdrop" role="img" aria-label="Faint watermark of a faceted geometric wall panel surface"></div>

  <svg class="card__stripe" width="1200" height="666" viewBox="0 0 1200 666" aria-hidden="true">
    <polygon points="678,0 708,0 424,666 392,666" fill="var(--stripe-green)"/>
  </svg>

  <section class="identity">
    <h1 class="identity__name"><span class="identity__first">Contact</span><span class="identity__last">Name</span></h1>
    <p class="identity__position">Position</p>
  </section>

  <ul class="contact">
    <li class="contact__item contact__item--mobile">
      <svg class="contact__icon" viewBox="0 0 30 30" aria-hidden="true"><rect x="9" y="2" width="12" height="26" rx="2" fill="none" stroke-width="2.5"/><circle cx="15" cy="24" r="1.5" stroke="none"/></svg>
      <span>+0198765432</span>
    </li>
    <li class="contact__item contact__item--address">
      <svg class="contact__icon" viewBox="0 0 30 30" aria-hidden="true"><polygon points="15,3 1,15 5,15 5,27 25,27 25,15 29,15" stroke="none"/><rect x="12" y="18" width="6" height="9" fill="var(--card-grey)" stroke="none"/></svg>
      <span>14 Larch Avenue,<br>Kelso Vale NSW 2190</span>
    </li>
    <li class="contact__item contact__item--email">
      <svg class="contact__icon" viewBox="0 0 30 30" aria-hidden="true"><rect x="1.5" y="5" width="27" height="20" fill="none" stroke-width="2.5"/><polyline points="1.5,5 15,17 28.5,5" fill="none" stroke-width="2.5"/><line x1="1.5" y1="25" x2="11" y2="14" stroke-width="2"/><line x1="19" y1="14" x2="28.5" y2="25" stroke-width="2"/></svg>
      <span>Sales@ripplecraft.com.au</span>
    </li>
    <li class="contact__item contact__item--phone">
      <svg class="contact__icon" viewBox="0 0 30 30" aria-hidden="true"><path d="M7 2 L12 9 L9 12 C11 17 13 19 18 21 L21 18 L28 23 L24 28 C13 27 3 17 2 6 Z" stroke="none"/></svg>
      <span>0291108450</span>
    </li>
    <li class="contact__item contact__item--fax">
      <svg class="contact__icon" viewBox="0 0 30 30" aria-hidden="true"><rect x="8" y="2" width="14" height="8" stroke="none"/><rect x="1" y="10" width="28" height="12" rx="2" stroke="none"/><rect x="7" y="17" width="16" height="11" fill="var(--card-grey)" stroke-width="2"/><line x1="10" y1="21" x2="20" y2="21" stroke-width="1.5"/><line x1="10" y1="24.5" x2="20" y2="24.5" stroke-width="1.5"/></svg>
      <span>029110846</span>
    </li>
    <li class="contact__item contact__item--web">
      <svg class="contact__icon" viewBox="0 0 30 30" aria-hidden="true"><circle cx="15" cy="15" r="13" stroke-width="2" fill="none"/><ellipse cx="15" cy="15" rx="6" ry="13" stroke-width="1.5" fill="none"/><line x1="2" y1="15" x2="28" y2="15" stroke-width="1.5"/><line x1="4" y1="9" x2="26" y2="9" stroke-width="1.5"/><line x1="4" y1="21" x2="26" y2="21" stroke-width="1.5"/></svg>
      <span>www.ripplecraft.com.au</span>
    </li>
  </ul>
</main>
</body>
</html>
```